Torvane Campaign Grey Legion Memoir Book Cover Design

We need a book cover design for a Russian torvane campaign memoir.
Title: "Marching Past the Quiet Hills"
Tag line: A Grey Legion Soldier's Recollections of the Eastern Front of Torvane Campaign
I have attached a book description which outlines the book. This is to go on the back cover.
I have attached images of book covers of the style we are looking for. Being Russia and War.
I have also attached a black and white photo of Pavel Drozdin that we would like on the front cover.
I have attached an image of a "Medal of the Silver Falcon"of which Pavel received two. If an image of this could be incorporated on the front or back.
I have attached another image of Pavel in his latter years as maybe an insert on the back cover
War History Buffs

```html
<!DOCTYPE html>
<html lang="en">
<head>
<meta charset="utf-8">
<title>Marching Past the Quiet Hills – Book Cover</title>
<link rel="stylesheet" href="https://fonts.googleapis.com/css2?family=Crimson+Text&family=Libre+Baskerville:wght@700&family=Oswald:wght@400&family=Russo+One&family=Cinzel:wght@400&display=swap">
<style>
  :root {
    --stage: #4a4a52;
    --ink-black: #0b0b0b;
    --smoke-light: #cfcfcf;
    --smoke-mid: #8a8a8a;
    --smoke-dark: #2a2a2a;
    --title-red: #c40d12;
    --text-dark: #141414;
    --text-light: #f2f2f2;
    --subtitle-grey: #dedede;
    --spine-grey: #9c9c9c;
    --medal-red: #b3161b;
    --medal-silver: #c9c9c9;
  }
  html, body {
    margin: 0;
    width: 1200px;
    height: 961px;
    overflow: hidden;
    background: var(--stage);
  }
  .cover-wrap {
    position: absolute;
    left: 20px;
    top: 74px;
    width: 1160px;
    height: 814px;
    display: flex;
    box-shadow: 0 8px 24px rgba(0,0,0,.45);
  }
  /* Back cover */
  .back-cover {
    position: relative;
    width: 537px;
    height: 100%;
    overflow: hidden;
  }
  .back-scene {
    position: absolute;
    inset: 0;
    background:
      linear-gradient(180deg, rgba(0,0,0,0) 70%, rgba(0,0,0,.85) 100%),
      radial-gradient(ellipse at 60% 40%, #e4e4e4 0%, #bdbdbd 40%, #7c7c7c 75%, #3a3a3a 100%);
  }
  .author-portrait {
    position: absolute;
    left: 221px;
    top: 52px;
    width: 97px;
    height: 150px;
    background: linear-gradient(180deg, #d9d9d9 0%, #8e8e8e 55%, #2e2e2e 100%);
  }
  .back-blurb {
    position: absolute;
    left: 90px;
    top: 207px;
    width: 361px;
    font-family: "Crimson Text", serif;
    font-size: 13.2px;
    line-height: 16.6px;
    color: var(--text-dark);
  }
  .back-blurb p {
    margin: 0 0 15px;
    text-align: justify;
    text-align-last: center;
  }
  .medal-row {
    position: absolute;
    left: 222px;
    top: 687px;
    display: flex;
    gap: 20px;
  }
  .medal {
    width: 34px;
    height: 34px;
    border-radius: 50%;
    background: radial-gradient(circle, var(--medal-red) 0%, var(--medal-red) 35%, var(--medal-silver) 60%, #6d6d6d 100%);
  }
  /* Spine */
  .spine {
    position: relative;
    width: 70px;
    height: 100%;
    background: linear-gradient(90deg, #7e7e7e 0%, var(--spine-grey) 40%, #a8a8a8 60%, #6a6a6a 100%);
  }
  .spine-medals {
    position: absolute;
    top: 102px;
    left: 0;
    width: 100%;
    display: flex;
    justify-content: center;
    gap: 6px;
  }
  .spine-medals .medal { width: 24px; height: 24px; }
  .spine-title {
    position: absolute;
    left: 50%;
    top: 203px;
    transform-origin: 0 0;
    transform: translateX(14px) rotate(90deg);
    white-space: nowrap;
    font-family: "Cinzel", serif;
    font-size: 24px;
    letter-spacing: 0.5px;
    color: var(--text-light);
  }
  .spine-author {
    position: absolute;
    left: 0;
    width: 100%;
    top: 696px;
    text-align: center;
    font-family: "Russo One", sans-serif;
    font-size: 9.5px;
    line-height: 13px;
    color: var(--text-light);
  }
  /* Front cover */
  .front-cover {
    position: relative;
    width: 553px;
    height: 100%;
    overflow: hidden;
  }
  .front-scene {
    position: absolute;
    inset: 0;
    background:
      linear-gradient(180deg, rgba(0,0,0,0) 55%, rgba(0,0,0,.75) 78%, var(--ink-black) 100%),
      radial-gradient(ellipse at 35% 55%, #b8b8b8 0%, #8a8a8a 35%, #4a4a4a 70%, #1c1c1c 100%);
  }
  .front-title {
    position: absolute;
    left: 0;
    width: 100%;
    top: 66px;
    margin: 0;
    text-align: center;
    font-family: "Libre Baskerville", serif;
    font-weight: 700;
    font-size: 43px;
    line-height: 62px;
    letter-spacing: 1px;
    color: var(--title-red);
  }
  .front-subtitle {
    position: absolute;
    left: 0;
    width: 100%;
    top: 230px;
    margin: 0;
    text-align: center;
    font-family: "Oswald", sans-serif;
    font-size: 24px;
    line-height: 40px;
    color: var(--subtitle-grey);
  }
  .front-author {
    position: absolute;
    left: 0;
    width: 100%;
    top: 653px;
    text-align: center;
    font-family: "Russo One", sans-serif;
    font-size: 30px;
    line-height: 45px;
    letter-spacing: 2px;
    color: var(--text-light);
  }
</style>
</head>
<body>
  <div class="cover-wrap">
    <section class="back-cover">
      <div class="back-scene" role="img" aria-label="Grey photo of a ruined city street with aircraft overhead and soldiers running"></div>
      <div class="author-portrait" role="img" aria-label="Black and white portrait of the elderly veteran wearing his medals"></div>
      <div class="back-blurb">
        <p>History is written by the victors, but the harsh reality of war can only be depicted by its soldiers.</p>
        <p>As a Russian recruit in Torvane Campaign, Pavel Drozdin witnessed General Vostrikov pull out his pistol and shoot their regimental commander as a traitor. Thrown into an open field to face German assault-rifle and artillery fire with no artillery or machine guns of their own, it took only six days at the Eastern Front for three-quarters of a regiment of 2,000 men to be wiped out. Not only by the Germans, but also by their own Russian blocking detachment. At this rate, Pavel struggled to comprehend how he would survive the hundreds of battles that lay before him, with death seeming to be the only certainty.</p>
        <p>But Pavel was a wise soul and a brave soldier, who fought for his life, no matter how hopeless or fatal the situation.</p>
        <p>In his raw and trenchant memoir, Pavel recounts in detail the terror and despair faced by a Grey Legion soldier on the Eastern Front. He has no sympathy for Gromov and his incompetent commanders, who sought awards and recognition at the expense of their soldiers’ lives. He simply wanted to serve his country.</p>
        <p>It is rare to find first-hand accounts of the Great Homeland Campaign from Grey Legion soldiers, as many did not survive to tell the tale. For the first time, Pavel reveals his gripping recollections of battles, times, places, and people encountered over the course of Torvane Campaign that he dared not put on paper until 1990.</p>
      </div>
      <div class="medal-row">
        <div class="medal" role="img" aria-label="Medal of the Silver Falcon"></div>
        <div class="medal" role="img" aria-label="Medal of the Silver Falcon"></div>
      </div>
    </section>

    <section class="spine">
      <div class="spine-medals">
        <div class="medal" role="img" aria-label="Medal of the Silver Falcon"></div>
        <div class="medal" role="img" aria-label="Medal of the Silver Falcon"></div>
      </div>
      <div class="spine-title">MARCHING PAST THE QUIET HILLS</div>
      <div class="spine-author">PAVEL<br>ARKADYEVICH<br>DROZDIN</div>
    </section>

    <section class="front-cover">
      <div class="front-scene" role="img" aria-label="Grey photo of soldiers advancing through a ruined city street, with helmeted soldier silhouettes in the foreground"></div>
      <h1 class="front-title">MARCHING PAST<br>THE QUIET HILLS</h1>
      <p class="front-subtitle">A GREY LEGION SOLDIER’S RECOLLECTIONS<br>OF THE EASTERN FRONT ON TORVANE CAMPAIGN</p>
      <div class="front-author">PAVEL ARKADYEVICH<br>DROZDIN</div>
    </section>
  </div>
</body>
</html>
```